Sell the dream! Property investment proposal document

We are looking for a proposal document which outlines our vision for property development. The purpose of the document is to raise investment from investors - sell the dream!
Brief summary:
Kestrel Dwellings Developments, is an emerging New Zealand property investment company with a focus on providing unique property investment opportunities.
Our expertise and capabilities in architectural modular homes provide us with a remarkable advantage in tackling the development of properties that are typically considered challenging, remote, or uniquely positioned.
Our specialization in this niche sector of property development not only sets us apart from competitors, but also paves the way for lucrative investment opportunities in the New Zealand property market.
Feel free to use any images from www.kestreldwellings.co.nz
Target Market(s)
investors for a unique property development opportunity
Industry/Entity Type
luxury property development in unique locations throughout New Zealand
Colors
Designer to choose only greyscale colors for use in the design.
Look and feel

```html
<!DOCTYPE html>
<html lang="en">
<head>
<meta charset="UTF-8">
<title>Kestrel Dwellings — Investment Proposal Covers</title>
<link rel="stylesheet" href="https://fonts.googleapis.com/css2?family=Manrope:wght@300;400&family=Inter+Tight:wght@400;500&family=Roboto+Condensed:wght@300&display=swap">
<style>
  :root {
    --backdrop: #e8e8e7;
    --ink: #111111;
    --ink-soft: #1c1c1c;
    --paper: #f3f3f2;
    --white: #ffffff;
    --rule: rgba(255,255,255,0.55);
    --sky: #cdbfa4;
    --sea: #9d9887;
    --hill: #4d4a2e;
    --field: #2f3320;
  }
  * { box-sizing: border-box; margin: 0; padding: 0; }
  html, body {
    width: 896px;
    height: 1200px;
    overflow: hidden;
    background: var(--backdrop);
  }
  .sheet {
    position: relative;
    width: 896px;
    height: 1200px;
  }
  .page {
    position: absolute;
    left: 88px;
    width: 720px;
    height: 561px;
    overflow: hidden;
    box-shadow: 0 6px 18px rgba(0,0,0,0.12);
  }
  .front-cover { top: 26px; background: var(--paper); }
  .back-cover { top: 613px; background: var(--ink-soft); }

  /* Front cover */
  .cover-photo {
    position: absolute;
    left: 0; top: 0;
    width: 720px; height: 424px;
    background: linear-gradient(180deg,
      var(--sky) 0%,
      #bfb49c 18%,
      var(--sea) 30%,
      #8e8a78 48%,
      var(--hill) 62%,
      var(--field) 80%,
      #262916 100%);
  }
  .cover-title {
    position: absolute;
    right: 40px; top: 48px;
    font-family: "Manrope", sans-serif;
    font-weight: 300;
    font-size: 88px;
    letter-spacing: -3px;
    line-height: 1;
    color: var(--white);
  }
  .doc-label {
    position: absolute;
    left: 0; top: 360px;
    width: 330px; height: 128px;
    background: var(--ink);
    padding: 24px 0 0 40px;
    font-family: "Roboto Condensed", sans-serif;
    font-weight: 300;
    font-size: 36px;
    line-height: 1.2;
    letter-spacing: 0.5px;
    color: var(--white);
    text-transform: uppercase;
  }
  .brand-lockup {
    position: absolute;
    right: 40px; top: 462px;
    display: flex;
    align-items: center;
    gap: 16px;
    color: var(--ink);
  }
  .brand-name {
    font-family: "Inter Tight", sans-serif;
    font-weight: 500;
    font-size: 26px;
    letter-spacing: -0.5px;
  }
  .brand-tagline {
    font-family: "Inter Tight", sans-serif;
    font-weight: 500;
    font-size: 17px;
    line-height: 1.05;
  }
  .brand-square {
    width: 10px; height: 10px;
    background: var(--ink);
  }

  /* Back cover */
  .back-lockup {
    position: absolute;
    left: 84px; top: 318px;
    display: flex;
    align-items: flex-end;
    gap: 28px;
    color: var(--white);
  }
  .back-lockup .brand-name {
    font-family: "Manrope", sans-serif;
    font-weight: 400;
    font-size: 28px;
    letter-spacing: -0.5px;
    line-height: 1;
  }
  .back-lockup .brand-tagline {
    font-size: 7px;
    font-weight: 400;
    line-height: 1.15;
    padding-bottom: 4px;
  }
  .contact-list {
    position: absolute;
    left: 84px; top: 380px;
    width: 168px;
    list-style: none;
    font-family: "Inter Tight", sans-serif;
    font-size: 9.5px;
    color: var(--white);
  }
  .contact-item {
    display: flex;
    align-items: center;
    gap: 10px;
    height: 28px;
    border-bottom: 1px solid var(--rule);
  }
  .contact-icon {
    width: 12px; height: 12px;
    flex: none;
  }
</style>
</head>
<body>
<main class="sheet">

  <section class="page front-cover">
    <div class="cover-photo" role="img" aria-label="Dusk photograph of a long low modular timber home on coastal grassland, sea and distant hills behind"></div>
    <h1 class="cover-title">Kestrel</h1>
    <p class="doc-label">Investment<br>Proposal</p>
    <div class="brand-lockup">
      <span class="brand-square"></span>
      <span class="brand-name">Kestrel</span>
      <span class="brand-tagline">Modular<br>Architectural<br>Homes</span>
    </div>
  </section>

  <section class="page back-cover">
    <div class="back-lockup">
      <span class="brand-name">Kestrel</span>
      <span class="brand-tagline">Modular<br>Architectural<br>Homes</span>
    </div>
    <ul class="contact-list">
      <li class="contact-item">
        <svg class="contact-icon" viewBox="0 0 12 12"><circle cx="6" cy="6" r="6" fill="#fff"/><path d="M4 3.2l1 .1.5 1.4-.7.6c.3.8.9 1.4 1.7 1.7l.6-.7 1.4.5.1 1c-.3.5-1 .7-1.6.5C5.3 7.8 4.2 6.7 3.7 5 3.5 4.3 3.6 3.6 4 3.2z" fill="#1c1c1c"/></svg>
        <span>09 555 0142</span>
      </li>
      <li class="contact-item">
        <svg class="contact-icon" viewBox="0 0 12 12"><circle cx="6" cy="6" r="6" fill="#fff"/><rect x="3" y="4" width="6" height="4.2" fill="none" stroke="#1c1c1c" stroke-width="0.8"/><path d="M3 4l3 2.3L9 4" fill="none" stroke="#1c1c1c" stroke-width="0.8"/></svg>
        <span>sales@kestreldwellings.co.nz</span>
      </li>
      <li class="contact-item">
        <svg class="contact-icon" viewBox="0 0 12 12"><circle cx="6" cy="6" r="6" fill="#fff"/><circle cx="6" cy="6" r="3" fill="none" stroke="#1c1c1c" stroke-width="0.8"/><path d="M3 6h6M6 3c-1.3 1.6-1.3 4.4 0 6M6 3c1.3 1.6 1.3 4.4 0 6" fill="none" stroke="#1c1c1c" stroke-width="0.7"/></svg>
        <span>www.kestreldwellings.co.nz</span>
      </li>
    </ul>
  </section>

</main>
</body>
</html>
```